Ridgeline Orchards Organic Cherry POS card 7x11

We are wanting to create a one-sided 7 x 11 organic cherry card that is eye catching and informative.This should be clear and easy to read and not cluttered. We use these cards as a display in grocery stores, demo stands, and other events to market Organic Ridgeline Sweet Orchards. We have a few facts that we would like displayed on the card (see attachment).

Target Market(s)

Consumers

Industry/Entity Type

Agriculture

Requirements
Must have
• Natural color palettes
• Easy to read
• Ridgeline Orchards
Nice to have
• Unique, realistic cherry design

```html
<!DOCTYPE html>
<html lang="en">
<head>
<meta charset="utf-8">
<title>Ridgeline Orchards – Organic Cherry POS Card</title>
<link href="https://fonts.googleapis.com/css2?family=Josefin+Sans:wght@400;600&family=Dancing+Script:wght@500&display=swap" rel="stylesheet">
<style>
  :root {
    --paper: #ffffff;
    --blush: #f07177;
    --wine: #621e2a;
    --ink: #2b1a1c;
    --cherry-light: #e8333c;
    --cherry-dark: #a5101b;
    --chalk: #ffffff;
  }
  * { margin: 0; padding: 0; box-sizing: border-box; }
  html, body { width: 1200px; height: 880px; overflow: hidden; background: var(--paper); }
  .card {
    position: relative;
    width: 1200px;
    height: 880px;
    background: var(--paper);
    font-family: "Josefin Sans", sans-serif;
  }
  .card__field {
    position: absolute;
    left: 0; top: 58px;
    width: 1200px; height: 764px;
  }
  .fact {
    position: absolute;
    color: var(--ink);
    font-size: 29px;
    font-weight: 600;
    letter-spacing: 0.32em;
    line-height: 1;
    text-transform: uppercase;
  }
  .fact span { display: block; }
  .fact--share { left: 37px; top: 110px; }
  .fact--share span { height: 58px; }
  .fact--state { right: 32px; top: 467px; text-align: right; }
  .fact--state span { height: 44px; }
  .benefits {
    position: absolute;
    left: 700px; top: 100px;
    width: 420px;
    color: var(--chalk);
    font-family: "Dancing Script", cursive;
    font-size: 25px;
    line-height: 1;
  }
  .benefits li { position: absolute; list-style: none; white-space: nowrap; transform: translateX(-50%); }
  .benefits__title { position: absolute; white-space: nowrap; transform: translateX(-50%); font-size: 27px; }
  .brand {
    position: absolute;
    left: 37px; top: 695px;
    display: flex; align-items: center; gap: 18px;
    color: var(--chalk);
    font-family: "Josefin Sans", sans-serif;
    font-weight: 600;
    font-size: 38px;
    letter-spacing: 0.12em;
    text-transform: uppercase;
  }
  .brand__dot { width: 46px; height: 46px; border: 3px solid var(--chalk); border-radius: 50%; }
</style>
</head>
<body>
<main class="card">
  <svg class="card__field" width="1200" height="764" viewBox="0 58 1200 764">
    <defs>
      <radialGradient id="cherryTone" cx="50%" cy="55%" r="60%">
        <stop offset="0%" stop-color="var(--cherry-light)"/>
        <stop offset="100%" stop-color="var(--cherry-dark)"/>
      </radialGradient>
    </defs>
    <rect class="field__blush" x="0" y="58" width="1200" height="764" fill="var(--blush)"/>
    <polygon class="field__band" points="0,566 1200,756 1200,822 0,822" fill="var(--wine)"/>
    <rect class="field__cherries" x="380" y="240" width="360" height="312" rx="150" fill="url(#cherryTone)" role="img" aria-label="Photo of two red cherries with their stems crossed to form a heart"/>
    <circle class="benefits__ring" cx="920" cy="248" r="144" fill="none" stroke="var(--chalk)" stroke-opacity="0.55" stroke-width="5"/>
    <g class="benefits__arrow" fill="none" stroke="var(--chalk)" stroke-width="2" stroke-linecap="round">
      <path d="M796 300 Q750 312 722 336"/>
      <path d="M722 336 L734 322 M722 336 L738 337"/>
    </g>
  </svg>

  <h2 class="fact fact--share">
    <span>Organic</span>
    <span>Ridgeline Orchards</span>
    <span>Make up 1/3</span>
    <span>of the nation’s</span>
    <span>production.</span>
  </h2>

  <div class="benefits">
    <p class="benefits__title" style="left:228px; top:8px;">Health benefits:</p>
    <ul>
      <li style="left:228px; top:50px;">fat free</li>
      <li style="left:180px; top:90px;">source of vitamin C</li>
      <li style="left:192px; top:134px;">a natural anti-inflammatory</li>
      <li style="left:236px; top:178px;">source of potassium</li>
      <li style="left:208px; top:220px;">source of melatonin</li>
    </ul>
  </div>

  <h2 class="fact fact--state">
    <span>Washington State</span>
    <span>is the nation’s</span>
    <span>largest producer</span>
    <span>of organic</span>
    <span>cherries.</span>
  </h2>

  <div class="brand">
    <span class="brand__dot"></span>
    <span class="brand__name">Ridgeline Orchards</span>
  </div>
</main>
</body>
</html>
```